Redesign of business card for Cedar Ridge Mechanical

We are looking for a new design for our business cards for Cedar Ridge Mechanical. We are a plumbing & HVAC construction company, operating on the West Coast of Canada and USA. Logo attached.
Industry/Entity Type
Construction - Plumbing & HVAC
Contact Information for Business Card
Name, address, phone numbers, email, website address
Look and feel
Each slider illustrates characteristics of the customer's brand and the style your logo design should communicate.

```html
<!DOCTYPE html>
<html lang="en">
<head>
<meta charset="utf-8">
<title>Cedar Ridge Mechanical – Business Card</title>
<link href="https://fonts.googleapis.com/css2?family=Figtree:wght@400;500;600;700&display=swap" rel="stylesheet">
<style>
  :root {
    --backdrop: #d6d6d6;
    --card: #ffffff;
    --ink: #111111;
    --ink-soft: #555555;
    --ink-mid: #333333;
    --band-grey: #8c8c8c;
  }
  * { margin: 0; padding: 0; box-sizing: border-box; }
  html, body { width: 1200px; height: 896px; overflow: hidden; }
  body {
    background: var(--backdrop);
    font-family: "Figtree", sans-serif;
    color: var(--ink);
    position: relative;
  }
  .card {
    position: absolute;
    left: 334px;
    width: 528px;
    height: 300px;
    background: var(--card);
    border-radius: 24px;
    overflow: hidden;
  }
  .card--front { top: 126px; }
  .card--back { top: 475px; }

  .wordmark {
    position: absolute;
    display: flex;
    align-items: center;
    gap: 12px;
    font-weight: 700;
    color: var(--ink);
    text-transform: uppercase;
    letter-spacing: 0.04em;
    line-height: 1.05;
  }
  .wordmark__square { background: var(--ink); flex: none; }
  .card--front .wordmark { left: 113px; top: 92px; font-size: 34px; }
  .card--front .wordmark__square { width: 52px; height: 52px; }
  .card--back .wordmark { left: 66px; top: 108px; font-size: 21px; gap: 10px; }
  .card--back .wordmark__square { width: 34px; height: 34px; }

  .divider {
    position: absolute;
    left: 295px; top: 67px;
    width: 1.5px; height: 166px;
    background: var(--ink-mid);
  }
  .contact { position: absolute; left: 309px; top: 62px; }
  .contact__name { font-size: 18px; font-weight: 600; letter-spacing: 0.01em; }
  .contact__role { font-size: 13.5px; color: var(--ink-soft); margin-top: 3px; }
  .contact__address { font-size: 13.5px; color: var(--ink-mid); margin-top: 14px; line-height: 21px; }
  .contact__list { list-style: none; margin-top: 10px; }
  .contact__list li {
    display: flex; align-items: center; gap: 6px;
    font-size: 13.5px; color: var(--ink-mid); height: 21px;
  }
  .contact__list svg { width: 12px; height: 12px; flex: none; }

  .wave { position: absolute; left: 0; top: 0; width: 528px; height: 300px; }
  .website {
    position: absolute; left: 36px; top: 268px;
    font-size: 13px; color: var(--card); letter-spacing: 0.01em;
  }
</style>
</head>
<body>
  <section class="card card--front">
    <div class="wordmark"><span class="wordmark__square"></span><span>Cedar Ridge<br>Mechanical</span></div>
  </section>

  <section class="card card--back">
    <div class="wordmark"><span class="wordmark__square"></span><span>Cedar Ridge<br>Mechanical</span></div>
    <div class="divider"></div>
    <div class="contact">
      <p class="contact__name">DANIEL FOSTER</p>
      <p class="contact__role">Managing Director</p>
      <p class="contact__address">Your address, City<br>State, Zip 1234</p>
      <ul class="contact__list">
        <li><svg viewBox="0 0 24 24"><path fill="currentColor" d="M6.6 10.8a15.1 15.1 0 0 0 6.6 6.6l2.2-2.2a1 1 0 0 1 1-.25 11.4 11.4 0 0 0 3.6.57 1 1 0 0 1 1 1V20a1 1 0 0 1-1 1A17 17 0 0 1 3 4a1 1 0 0 1 1-1h3.5a1 1 0 0 1 1 1c0 1.25.2 2.45.57 3.57a1 1 0 0 1-.25 1z"/></svg>123 456 789</li>
        <li><svg viewBox="0 0 24 24"><rect x="6" y="2" width="12" height="20" rx="2" fill="none" stroke="currentColor" stroke-width="2.2"/><circle cx="12" cy="18" r="1.3" fill="currentColor"/></svg>123 456 789</li>
        <li><svg viewBox="0 0 24 24"><rect x="2" y="5" width="20" height="14" rx="1.5" fill="none" stroke="currentColor" stroke-width="2.2"/><path d="M3 6l9 7 9-7" fill="none" stroke="currentColor" stroke-width="2.2"/></svg>info@yourgmail.com</li>
      </ul>
    </div>
    <svg class="wave" viewBox="0 0 528 300" aria-hidden="true">
      <path fill="var(--band-grey)" d="M200 252 C330 272 430 276 528 250 L528 300 L0 300 Z"/>
      <path fill="var(--card)" d="M0 266 C90 232 220 242 330 269 C420 289 480 287 528 281 L528 300 L0 300 Z"/>
      <path fill="var(--ink)" d="M0 271 C90 238 220 247 330 274 C420 293 480 291 528 287 L528 300 L0 300 Z"/>
      <path fill="none" stroke="var(--ink)" stroke-width="2.5" d="M0 262 C90 228 220 238 330 265"/>
    </svg>
    <p class="website">www.yourwebsite.com</p>
  </section>
</body>
</html>
```